Winelabel for Italian Wine incl. box.

Front and back label for new Italian wine.
It´s a premium redwine,
Size of Labels: Front 100x115 | Back 60x85
For front label we can also use these sizes:
95X115 - 100x100 – 86x97 – 100x110
For back labels : 60X90 – 60X95 – 60X100
We can only use one type of foil finishing.
BRAND = CREDALI sul` Passo Vellino (in 2 lines)
2. titel = Vino della Serpola
Semi lines = Ancient vinification Traditions | Truscany
Style = elegant Italian coloured Harlequin,
Other colors using white/black/gold
Include a round "water-mark" with text : Selected for loyal winelowers
Back label will be short story + legal data + barcode.
Outer box of 6 bottles case design print on all 4 fronts.

```html
<!DOCTYPE html>
<html lang="it">
<head>
<meta charset="utf-8">
<title>CREDALI sul` Passo Vellino – Front Label</title>
<link rel="stylesheet" href="https://fonts.googleapis.com/css2?family=Old+Standard+TT:wght@400;700&family=Cormorant+Garamond:wght@400;500&display=swap">
<style>
  :root {
    --backdrop: #4a3628;
    --label-paper: #f1f0ea;
    --ink: #1d1c1a;
    --harlequin-red: #c0343a;
    --harlequin-green: #3f6b4c;
    --gold: #a4844f;
  }
  html, body {
    margin: 0;
    width: 1200px;
    height: 900px;
    overflow: hidden;
    background: var(--backdrop);
  }
  .front-label {
    position: absolute;
    left: 312px;
    top: 50px;
    width: 575px;
    height: 800px;
    background: var(--label-paper);
    overflow: hidden;
    color: var(--ink);
    text-align: center;
  }
  .brand-name {
    position: absolute;
    top: 128px;
    left: 0;
    right: 0;
    margin: 0;
    font-family: "Old Standard TT", serif;
    font-weight: 400;
    font-size: 84px;
    letter-spacing: 1px;
    line-height: 1;
  }
  .brand-subline {
    position: absolute;
    top: 214px;
    left: 0;
    right: 0;
    margin: 0;
    font-family: "Cormorant Garamond", serif;
    font-size: 22px;
    color: var(--harlequin-red);
    letter-spacing: 0.5px;
  }
  .harlequin-illustration {
    position: absolute;
    left: 118px;
    top: 248px;
    width: 350px;
    height: 360px;
    background: radial-gradient(ellipse at 50% 55%, #8d7d70 0%, #b9b0a4 45%, var(--label-paper) 78%);
  }
  .loyalty-seal {
    position: absolute;
    left: 470px;
    top: 250px;
    width: 160px;
    height: 160px;
  }
  .tradition-line {
    position: absolute;
    top: 672px;
    left: 0;
    right: 0;
    margin: 0;
    font-family: "Old Standard TT", serif;
    font-size: 15px;
    letter-spacing: 0.5px;
    text-transform: uppercase;
  }
  .wine-type {
    position: absolute;
    top: 706px;
    left: 0;
    right: 0;
    margin: 0;
    font-family: "Cormorant Garamond", serif;
    font-size: 15px;
  }
  .volume-info {
    position: absolute;
    top: 728px;
    left: 0;
    right: 0;
    margin: 0;
    font-family: "Cormorant Garamond", serif;
    font-size: 12px;
  }
</style>
</head>
<body>
  <section class="front-label">
    <h1 class="brand-name">CREDALI</h1>
    <p class="brand-subline">sul` Passo Vellino</p>

    <div class="harlequin-illustration" role="img" aria-label="Engraved harlequin jester in profile with red and green cap and ruff collar"></div>

    <svg class="loyalty-seal" viewBox="0 0 160 160" aria-label="Round seal: Selected for loyal winelovers">
      <defs>
        <path id="seal-ring" d="M80,80 m-56,0 a56,56 0 1,1 112,0 a56,56 0 1,1 -112,0"/>
      </defs>
      <circle cx="80" cy="80" r="68" fill="none" stroke="var(--gold)" stroke-width="1.2"/>
      <text font-family="Cormorant Garamond, serif" font-size="13" fill="var(--gold)" letter-spacing="1">
        <textPath href="#seal-ring">For loyal winelovers · For loyal winelovers ·</textPath>
      </text>
      <text x="80" y="84" text-anchor="middle" font-family="Old Standard TT, serif" font-size="11" fill="var(--gold)" letter-spacing="1">SELECTED</text>
    </svg>

    <p class="tradition-line">Ancient Vinification Traditions · Truscany</p>
    <p class="wine-type">Premium Italian Red Wine</p>
    <p class="volume-info">750 ml · 13,5% vol</p>
  </section>
</body>
</html>
```